Fitness Centre/Personal Trainer Business Card

We need a business card design for a company based in Singapore called 'Vigor Ledger'.

We are a team of Personal Trainers and we are planning to open our new training facility.

This design will also be printed/painted on the walls in our gym.

We are a new breed of personal trainers who take fitness seriously and holistically. We do not merely train our clients to be big and muscular.

We believe in wholeness. In our opinion, fitness should include: strength, speed, flexibility, mobility, stamina & agility. These are what we train for. Of course, nutrition/diet is key.

We use fitness tools such as kettlebells, QVL, Pylometric boxes, battling ropes, clubbells, medicine balls, bulgarian bags etc - functional and non-bulky tools.

I currently have a Facebook page 'Vigor Ledger SG' which shows a logo of a kettlebell. But my business focus has since changed.

Services provided:
- Kettlebell Sport Preparation
- Calisthenics Training
- Corrective Exercises
- Sports Strength & Conditioning
- 28 days Weight Loss Program
- Myofascial Rehab Therapy
- Sports/Thai Massage

Main colors for the design should be BLACK & YELLOW. We envision a design which is able to protray the holistic view we take on fitness. Also it should somewhat appeal to the ladies and not intimidate them.

Target Market(s)

People between 18-35 years old. Students and working class alike.

Industry/Entity Type

Training

Requirements
Must have
• Name: Marcus Obadiah Lim
Fitness Coach
Corrective Exercise Specialist
M: +65 9437 2065
E: marcus@sgvigorledger-example.com

Double-sided please.
Nice to have
• "What is your vigor ledger?"

```html
<!DOCTYPE html>
<html lang="en">
<head>
<meta charset="utf-8">
<title>Vigor Ledger – Business Card Set</title>
<link rel="stylesheet" href="https://fonts.googleapis.com/css2?family=Open+Sans:wght@400;600;700&display=swap">
<style>
  :root {
    --black: #050505;
    --yellow: #f7dc00;
    --white: #ffffff;
    --ink: #1a1a1a;
    --grey-text: #333333;
    --bullet-grey: #888888;
    --board-light: #e6e6e6;
    --board-mid: #cfcfcf;
    --board-dark: #a9a9a9;
    --divider: #555555;
  }
  * { margin: 0; padding: 0; box-sizing: border-box; }
  html, body { width: 1200px; height: 499px; overflow: hidden; }
  body {
    position: relative;
    font-family: "Open Sans", Arial, sans-serif;
    background: radial-gradient(ellipse at 50% 40%, var(--board-light) 0%, var(--board-mid) 60%, var(--board-dark) 100%);
  }

  .card {
    position: absolute;
    border-radius: 16px;
    overflow: hidden;
    box-shadow: 0 1px 3px rgba(0,0,0,.35);
  }
  .card--black { background: var(--black); }
  .card--white { background: var(--white); }

  .front { top: 25px; width: 372px; height: 211px; }
  .front--dark { left: 197px; }
  .front--light { left: 596px; }
  .back { top: 258px; width: 374px; height: 213px; }
  .back--centered { left: 20px; }
  .back--list { left: 421px; }
  .back--photo { left: 810px; }

  .front__wave { position: absolute; inset: 0; width: 100%; height: 100%; }

  /* Brand name block */
  .brand {
    position: absolute;
    display: flex; align-items: center; gap: 8px;
    font-weight: 700;
    white-space: nowrap;
  }
  .brand__dot { width: 26px; height: 26px; border-radius: 50%; background: var(--yellow); flex: none; }
  .brand--on-dark { color: var(--yellow); }
  .brand--on-light { color: var(--ink); }
  .front .brand { left: 50%; top: 62px; transform: translateX(-50%); font-size: 26px; }

  /* Front identity and contacts */
  .identity {
    position: absolute; right: 196px; top: 162px;
    text-align: right; color: var(--ink); font-size: 9.5px; line-height: 14px;
  }
  .identity__name { font-size: 12.5px; font-weight: 700; line-height: 15px; }
  .contact-rule { position: absolute; left: 181px; top: 164px; width: 1px; height: 42px; background: var(--divider); }
  .contact {
    position: absolute; left: 188px; top: 164px;
    list-style: none; color: var(--ink); font-size: 9.5px; line-height: 14px;
  }
  .contact li { display: flex; align-items: center; gap: 4px; }
  .contact svg { width: 8px; height: 8px; flex: none; }

  /* Shared back elements */
  .services-title { font-weight: 700; font-size: 14px; }
  .closing { position: absolute; left: 0; right: 0; top: 194px; text-align: center; font-weight: 700; font-size: 12px; }

  /* Back: centred services */
  .back--centered .services-title { position: absolute; left: 0; right: 0; top: 48px; text-align: center; color: var(--white); }
  .back--centered .services-grid {
    position: absolute; left: 0; right: 0; top: 79px;
    list-style: none; text-align: center; color: var(--yellow); font-size: 13px; line-height: 24px;
  }
  .back--centered .services-grid li { display: inline; }
  .back--centered .services-grid li::before { content: "• "; }
  .back--centered .closing { color: var(--white); letter-spacing: .6px; }

  /* Back: white list */
  .back--list .brand {
    left: 12px; top: 78px; width: 168px;
    flex-direction: column; gap: 10px; font-size: 22px;
  }
  .back--list .services-title { position: absolute; left: 191px; top: 18px; color: var(--grey-text); }
  .back--list .services-stack {
    position: absolute; left: 191px; top: 47px;
    list-style: none; color: var(--grey-text); font-size: 11.5px; line-height: 19px;
  }
  .back--list .services-stack li::before { content: "• "; color: var(--bullet-grey); }
  .back--list .closing { color: var(--grey-text); font-size: 12.5px; letter-spacing: .3px; }

  /* Back: photo version */
  .photo-fill {
    position: absolute; left: 0; top: 90px; width: 250px; height: 123px;
    background: radial-gradient(ellipse at 45% 55%, #5a5a5a 0%, #2a2a2a 45%, var(--black) 80%);
  }
  .back--photo .brand {
    left: 18px; top: 24px; width: 110px;
    flex-direction: column; gap: 6px; font-size: 17px;
  }
  .back--photo .brand__dot { width: 22px; height: 22px; }
  .back--photo .services-title { position: absolute; right: 13px; top: 21px; color: var(--white); }
  .back--photo .services-stack {
    position: absolute; right: 13px; top: 50px;
    list-style: none; text-align: right; color: var(--yellow); font-weight: 700; font-size: 11.5px; line-height: 21.3px;
  }
  .back--photo .services-stack li::before { content: "• "; }
</style>
</head>
<body>

<!-- Front, dark version -->
<section class="card card--black front front--dark">
  <svg class="front__wave" viewBox="0 0 372 211" preserveAspectRatio="none" aria-hidden="true">
    <path d="M0 128 Q170 178 372 118 L372 124 Q170 186 0 136 Z" fill="#cfcfcf"/>
    <path d="M0 136 Q170 186 372 124 L372 211 L0 211 Z" fill="#f7dc00"/>
  </svg>
  <div class="brand brand--on-dark"><span class="brand__dot"></span><span class="brand__name">Vigor Ledger</span></div>
  <div class="identity">
    <p class="identity__name">Marcus Obadiah Lim</p>
    <p>Fitness Coach</p>
    <p>Corrective Exercise Specialist</p>
  </div>
  <span class="contact-rule"></span>
  <ul class="contact">
    <li><svg viewBox="0 0 8 8"><rect x="2" y="0.5" width="4" height="7" rx="1" fill="#1a1a1a"/></svg>+65 9437 2065</li>
    <li><svg viewBox="0 0 8 8"><rect x="0.5" y="1.5" width="7" height="5" fill="#1a1a1a"/><path d="M0.5 1.5 L4 4.5 L7.5 1.5" stroke="#f7dc00" stroke-width=".8" fill="none"/></svg>marcus@sgvigorledger-example.com</li>
    <li><svg viewBox="0 0 8 8"><circle cx="4" cy="4" r="3.5" fill="#1a1a1a"/></svg>www.vigorledger-example.com</li>
  </ul>
</section>

<!-- Front, light version -->
<section class="card card--white front front--light">
  <svg class="front__wave" viewBox="0 0 372 211" preserveAspectRatio="none" aria-hidden="true">
    <path d="M0 128 Q170 178 372 118 L372 126 Q170 188 0 137 Z" fill="#050505"/>
    <path d="M0 137 Q170 188 372 126 L372 211 L0 211 Z" fill="#f7dc00"/>
  </svg>
  <div class="brand brand--on-light"><span class="brand__dot"></span><span class="brand__name">Vigor Ledger</span></div>
  <div class="identity">
    <p class="identity__name">Marcus Obadiah Lim</p>
    <p>Fitness Coach</p>
    <p>Corrective Exercise Specialist</p>
  </div>
  <span class="contact-rule"></span>
  <ul class="contact">
    <li><svg viewBox="0 0 8 8"><rect x="2" y="0.5" width="4" height="7" rx="1" fill="#1a1a1a"/></svg>+65 9437 2065</li>
    <li><svg viewBox="0 0 8 8"><rect x="0.5" y="1.5" width="7" height="5" fill="#1a1a1a"/><path d="M0.5 1.5 L4 4.5 L7.5 1.5" stroke="#f7dc00" stroke-width=".8" fill="none"/></svg>marcus@sgvigorledger-example.com</li>
    <li><svg viewBox="0 0 8 8"><circle cx="4" cy="4" r="3.5" fill="#1a1a1a"/></svg>www.vigorledger-example.com</li>
  </ul>
</section>

<!-- Back, centred services -->
<section class="card card--black back back--centered">
  <h2 class="services-title">Services</h2>
  <ul class="services-grid">
    <li>Sports Strength &amp; Conditioning</li> <li>Sports/Thai Massage</li><br>
    <li>Kettlebell Sport Preparation</li> <li>Corrective Exercises</li><br>
    <li>28 days Weight Loss Program</li> <li>Calisthenics Training</li><br>
    <li>Myofascial Rehab Therapy</li>
  </ul>
  <p class="closing">WHAT IS YOUR VIGOR LEDGER?</p>
</section>

<!-- Back, white list -->
<section class="card card--white back back--list">
  <div class="brand brand--on-light"><span class="brand__dot"></span><span class="brand__name">Vigor Ledger</span></div>
  <h2 class="services-title">Services</h2>
  <ul class="services-stack">
    <li>Sports Strength &amp; Conditioning</li>
    <li>Kettlebell Sport Preparation</li>
    <li>28 days Weight Loss Program</li>
    <li>Myofascial Rehab Therapy</li>
    <li>Calisthenics Training</li>
    <li>Corrective Exercises</li>
    <li>Sports/Thai Massage</li>
  </ul>
  <p class="closing">What is your vigor ledger?</p>
</section>

<!-- Back, photo version -->
<section class="card card--black back back--photo">
  <div class="photo-fill" role="img" aria-label="Photo of dumbbells resting on a dark gym floor"></div>
  <div class="brand brand--on-dark"><span class="brand__dot"></span><span class="brand__name">Vigor Ledger</span></div>
  <h2 class="services-title">Services</h2>
  <ul class="services-stack">
    <li>Sports Strength &amp; Conditioning</li>
    <li>Kettlebell Sport Preparation</li>
    <li>28 days Weight Loss Program</li>
    <li>Myofascial Rehab Therapy</li>
    <li>Calisthenics Training</li>
    <li>Corrective Exercises</li>
    <li>Sports/Thai Massage</li>
  </ul>
</section>

</body>
</html>
```